Business Card Design Project

We are rebranding an existing automotive collision repair business. The business is called dent haven. I have attached logo but I'm not tied to that. I want to leave this wide open.

I want this card to say we are professional, competent, cutting edge. We are focused on customers and use a lot of the latest technology to make the customer experience different. We sign customers in on iPads. Paperwork I signed electronically and updates are sent via text, email, logging on a website or as they wish. I want this innovation and image to come through in our cards

Target Market(s)

60%. Women 40% men. Age 35-60

Industry/Entity Type

Automotive

Requirements
Must have
• The card must have name, title, phone,email, cell, web page

```html
<!DOCTYPE html>
<html lang="en">
<head>
<meta charset="utf-8">
<title>Dent Haven – Business Card</title>
<link href="https://fonts.googleapis.com/css2?family=Roboto:wght@400;700&display=swap" rel="stylesheet">
<style>
  :root {
    --page-bg: #ffffff;
    --card-white: #ffffff;
    --card-border: #e3e3e3;
    --brand-green: #4bb848;
    --wordmark-green: #5aab3a;
    --ink-white: #ffffff;
    --note-ink: #111111;
    --shadow: rgba(0, 0, 0, 0.18);
  }
  * { box-sizing: border-box; margin: 0; padding: 0; }
  html, body {
    width: 1200px;
    height: 800px;
    overflow: hidden;
    background: var(--page-bg);
    font-family: "Roboto", Arial, sans-serif;
  }
  .canvas {
    position: relative;
    width: 1200px;
    height: 800px;
  }
  .card {
    position: absolute;
    left: 394px;
    width: 412px;
    height: 235px;
    border-radius: 12px;
    box-shadow: 0 14px 14px -10px var(--shadow);
  }
  .card-front {
    top: 133px;
    background: var(--card-white);
    border: 2px solid var(--card-border);
    display: flex;
    align-items: center;
    justify-content: center;
  }
  .wordmark {
    display: flex;
    align-items: center;
    gap: 8px;
    font-weight: 700;
    font-size: 28px;
    letter-spacing: 0.5px;
    color: var(--wordmark-green);
  }
  .wordmark-dot {
    width: 12px;
    height: 12px;
    border-radius: 50%;
    background: var(--wordmark-green);
  }
  .card-back {
    top: 436px;
    background: var(--brand-green);
    color: var(--ink-white);
  }
  .holder {
    position: absolute;
    top: 20px;
    right: 24px;
    text-align: right;
    font-size: 14px;
    line-height: 17px;
  }
  .contact-list {
    position: absolute;
    left: 24px;
    top: 134px;
    list-style: none;
    font-size: 13px;
  }
  .contact-list li {
    display: flex;
    align-items: center;
    gap: 12px;
    height: 22px;
  }
  .contact-icon {
    width: 14px;
    height: 14px;
    fill: none;
    stroke: var(--ink-white);
    stroke-width: 1.1;
  }
  .note {
    position: absolute;
    left: 0;
    right: 0;
    top: 772px;
    text-align: center;
    font-size: 15px;
    color: var(--note-ink);
  }
</style>
</head>
<body>
<main class="canvas">
  <section class="card card-front" aria-label="Card front">
    <div class="wordmark"><span class="wordmark-dot"></span><span>Dent Haven</span></div>
  </section>

  <section class="card card-back" aria-label="Card back">
    <div class="holder">
      <p class="holder-name">Mark Ellison</p>
      <p class="holder-title">Director</p>
    </div>
    <ul class="contact-list">
      <li>
        <svg class="contact-icon" viewBox="0 0 14 14"><rect x="1" y="3" width="12" height="8.5"/><path d="M1 3l6 5 6-5"/></svg>
        <span>hello@denthaven.com</span>
      </li>
      <li>
        <svg class="contact-icon" viewBox="0 0 14 14"><circle cx="7" cy="7" r="6"/><ellipse cx="7" cy="7" rx="2.6" ry="6"/><path d="M1 7h12M2 4h10M2 10h10"/></svg>
        <span>www.denthaven.com</span>
      </li>
      <li>
        <svg class="contact-icon" viewBox="0 0 14 14"><path d="M3 1.5l2.2 2.7-1.3 1.6c.8 1.7 2 2.9 3.6 3.7l1.6-1.3 2.7 2.2-1.5 1.8C6 11.8 2.2 8 1.2 3z"/></svg>
        <span>+1 (800) 555-0142</span>
      </li>
      <li>
        <svg class="contact-icon" viewBox="0 0 14 14"><rect x="3.5" y="1" width="7" height="12" rx="1"/><path d="M6 11h2"/></svg>
        <span>+1 (800) 555-0142</span>
      </li>
    </ul>
  </section>

  <p class="note">*Please note all content is dummy copy</p>
</main>
</body>
</html>
```